Business card for medical clinic

I need an upmarket, modern medical/health business card for my clinic

Contact Information for Business Card

name, address, email, qr code

```html
<!DOCTYPE html>
<html lang="en">
<head>
<meta charset="utf-8">
<title>Corvan Health Partners – Business Card</title>
<link href="https://fonts.googleapis.com/css2?family=Montserrat:wght@400;500;600&display=swap" rel="stylesheet">
<style>
  :root {
    --backdrop: #8a7760;
    --card-navy: #1e2946;
    --card-shadow: rgba(0, 0, 0, 0.55);
    --accent-blue: #2fa4de;
    --brand-blue: #2d6c9f;
    --text-light: #f2f4f8;
    --ring-light: #e4e7ee;
  }
  * { margin: 0; padding: 0; box-sizing: border-box; }
  html, body {
    width: 900px;
    height: 1200px;
    overflow: hidden;
  }
  body {
    position: relative;
    background: var(--backdrop);
    font-family: "Montserrat", sans-serif;
    color: var(--text-light);
  }
  .card {
    position: absolute;
    background: var(--card-navy);
    border-radius: 24px;
    box-shadow: 0 6px 18px var(--card-shadow);
  }
  .card-front { left: 80px; top: 130px; width: 742px; height: 442px; }
  .card-back  { left: 78px; top: 638px; width: 744px; height: 440px; }

  .front-brand {
    position: absolute;
    left: 34px;
    top: 44px;
    font-size: 22px;
    font-weight: 500;
    letter-spacing: 1.5px;
    line-height: 26px;
    text-transform: uppercase;
    color: var(--brand-blue);
  }
  .holder {
    position: absolute;
    right: 50px;
    top: 40px;
    text-align: right;
  }
  .holder-name {
    font-size: 24px;
    font-weight: 600;
    color: var(--accent-blue);
    line-height: 1.2;
  }
  .holder-title {
    font-size: 15px;
    font-weight: 400;
    margin-top: 4px;
  }
  .address {
    position: absolute;
    left: 41px;
    top: 251px;
    font-size: 16px;
    line-height: 20px;
    font-style: normal;
  }
  .contact-list {
    position: absolute;
    left: 40px;
    top: 323px;
    list-style: none;
  }
  .contact-item {
    display: flex;
    align-items: center;
    height: 31.5px;
    font-size: 16px;
  }
  .contact-icon {
    width: 16px;
    height: 16px;
    margin-right: 11px;
    fill: var(--accent-blue);
  }

  .back-brand {
    position: absolute;
    left: 134px;
    top: 140px;
    display: flex;
    align-items: center;
  }
  .brand-ring {
    width: 180px;
    height: 180px;
    border: 5px solid var(--ring-light);
    border-radius: 50%;
    flex-shrink: 0;
  }
  .back-brand-name {
    margin-left: 26px;
    font-size: 31px;
    font-weight: 500;
    letter-spacing: 1.5px;
    line-height: 1.25;
    text-transform: uppercase;
    color: var(--text-light);
  }
</style>
</head>
<body>

  <section class="card card-front" aria-label="Card front">
    <div class="front-brand">Corvan Health<br>Partners</div>

    <div class="holder">
      <div class="holder-name">Daniel Hart</div>
      <div class="holder-title">Managing Director</div>
    </div>

    <address class="address">
      245 Cedar Ridge Lane<br>
      Fairview, MS 39120
    </address>

    <ul class="contact-list">
      <li class="contact-item">
        <svg class="contact-icon" viewBox="0 0 24 24" aria-hidden="true">
          <path d="M6.6 10.8a15.1 15.1 0 0 0 6.6 6.6l2.2-2.2a1 1 0 0 1 1-.25 11.4 11.4 0 0 0 3.6.57 1 1 0 0 1 1 1V20a1 1 0 0 1-1 1A17 17 0 0 1 3 4a1 1 0 0 1 1-1h3.5a1 1 0 0 1 1 1c0 1.25.2 2.45.57 3.57a1 1 0 0 1-.25 1z"/>
        </svg>
        888.555.0142
      </li>
      <li class="contact-item">
        <svg class="contact-icon" viewBox="0 0 24 24" aria-hidden="true">
          <path d="M2 5h20v2l-10 6L2 7z M2 9l10 6 10-6v10H2z"/>
        </svg>
        hello@corvanhealth.com
      </li>
      <li class="contact-item">
        <svg class="contact-icon" viewBox="0 0 24 24" aria-hidden="true">
          <circle cx="12" cy="12" r="10"/>
          <path d="M2 12h20M12 2c3 3 3 17 0 20M12 2c-3 3-3 17 0 20" stroke="#1e2946" stroke-width="1.6" fill="none"/>
        </svg>
        www.corvanhealth.com
      </li>
    </ul>
  </section>

  <section class="card card-back" aria-label="Card back">
    <div class="back-brand">
      <div class="brand-ring"></div>
      <div class="back-brand-name">Corvan Health<br>Partners</div>
    </div>
  </section>

</body>
</html>
```